KTWG application splash screen

We need a 1024x768 image for use as an application splash screen.
The image will be displayed full screen on an 10 inch industrial PC 1024x768 screen while our application is launching. The image should convey that the application is "Waiting for connection to Wi-Fi access point..." and include a graphic of the industrial PC connected to the access point via an Ethernet cable. A list of troubleshooting steps should be included at the bottom of the image. The troubleshooting steps should not be the main focus of the image and should be shown in a smaller font (but still readable at 1024x768 displayed on a 10 inch screen).
I will include a mock up of the general idea of what we are looking for as well as image files for the industrial PC, a screenshot of our application to show on the PC's screen and the AP.
For general look and feel and a sense of corporate branding please review our website https://marrowgatesoilworks.example/. The splash screen should reflect corporate branding.
Target Market(s)
Users of our application
Industry/Entity Type
Agriculture
Look and feel

```html
<!DOCTYPE html>
<html lang="en">
<head>
<meta charset="utf-8">
<title>KTWG application splash screen</title>
<link rel="stylesheet" href="https://fonts.googleapis.com/css2?family=Quicksand:wght@500;600;700&display=swap">
<style>
  :root {
    --page: #ffffff;
    --screen-bg: #f6f6f8;
    --green-light: #b3e8bd;
    --green-mid: #1fa36c;
    --green-deep: #0c7d53;
    --green-brand: #26a96a;
    --text-dark: #2f3437;
    --text-muted: #4a4f53;
    --white: #ffffff;
    --pc-dark: #1b1b1b;
    --pc-light: #e9e9ee;
    --ap-body: #f1f3f2;
  }
  * { margin: 0; padding: 0; box-sizing: border-box; }
  html, body {
    width: 1200px; height: 1200px; overflow: hidden;
    background: var(--page);
    font-family: "Quicksand", sans-serif;
  }
  .splash {
    position: absolute; left: 60px; top: 195px;
    width: 1081px; height: 810px;
    background: var(--screen-bg);
    overflow: hidden;
  }
  .hero {
    position: absolute; left: 0; top: 0;
    width: 1081px; height: 649px;
    border-radius: 0 0 95px 95px;
    background:
      radial-gradient(ellipse 520px 380px at 30px 20px, var(--green-light) 0%, rgba(120,210,150,0.55) 35%, rgba(31,163,108,0) 100%),
      linear-gradient(135deg, var(--green-mid) 0%, #19995f 55%, var(--green-deep) 100%);
    border-bottom: 3px solid #3cbf7f;
  }
  .headline {
    position: absolute; left: 0; right: 0; top: 226px;
    text-align: center;
    color: var(--white);
    font-weight: 600; font-size: 34px; letter-spacing: 0.2px;
  }
  .connection-diagram { position: absolute; left: 0; top: 0; }
  .troubleshooting {
    position: absolute; left: 47px; top: 684px;
    color: var(--text-dark);
  }
  .troubleshooting-label {
    display: inline-block;
    background: var(--green-brand); color: var(--white);
    font-size: 10.5px; font-weight: 600;
    padding: 3px 10px 4px; border-radius: 10px;
  }
  .steps { list-style: none; margin-top: 9px; }
  .step { font-size: 10px; font-weight: 600; margin-bottom: 5px; display: flex; align-items: center; gap: 4px; }
  .step-num {
    display: inline-flex; width: 10px; height: 10px; border-radius: 50%;
    border: 1px solid var(--green-brand); color: var(--green-brand);
    font-size: 7px; align-items: center; justify-content: center; margin-left: 4px;
  }
  .substeps { list-style: none; margin: 0 0 0 20px; }
  .substep { font-size: 8.8px; font-weight: 500; color: var(--text-muted); line-height: 10.3px; }
  .substep::before { content: "• "; }
  .brand-mark {
    position: absolute; left: 930px; top: 722px;
    display: flex; align-items: center; gap: 8px;
    color: var(--green-brand); font-weight: 700; font-size: 30px;
  }
  .brand-mark .square { width: 22px; height: 22px; background: var(--green-brand); border-radius: 4px; }
</style>
</head>
<body>
  <main class="splash">
    <section class="hero">
      <h1 class="headline">Waiting for connection to Wi-Fi access point...</h1>
      <svg class="connection-diagram" width="1081" height="649" viewBox="0 0 1081 649">
        <defs>
          <linearGradient id="pc-tone" x1="0" y1="0" x2="0" y2="1">
            <stop offset="0" stop-color="var(--pc-light)"/>
            <stop offset="1" stop-color="#9fa3a6"/>
          </linearGradient>
        </defs>
        <path class="cable" d="M385 454 V462 Q385 467 390 467 H650 Q655 467 655 462 V448 Q655 443 660 443 H791"
              fill="none" stroke="#ffffff" stroke-width="1.6" stroke-dasharray="6 4"/>
        <rect class="industrial-pc" role="img" aria-label="Industrial panel PC showing the application dashboard"
              x="239" y="337" width="159" height="117" rx="6" fill="url(#pc-tone)"/>
        <rect class="access-point" role="img" aria-label="Outdoor Wi-Fi access point with two antennas"
              x="791" y="334" width="16" height="124" rx="4" fill="var(--ap-body)"/>
      </svg>
    </section>

    <section class="troubleshooting">
      <span class="troubleshooting-label">Troubleshooting steps:</span>
      <ol class="steps">
        <li class="step"><span class="step-num">1</span>This screen should only be visible for a short time on boot.</li>
        <li class="step"><span class="step-num">2</span>If this screen stays visible for more than a minute:</li>
      </ol>
      <ul class="substeps">
        <li class="substep">Verify that the Wi-Fi Access Point (AP) powers up when this system does (indicated by a green light on the side of the AP).</li>
        <li class="substep">Check the Ethernet cable between this system and the AP for damage, and replace it if necessary.</li>
        <li class="substep">Power-cycle this system and wait for it to reboot fully.</li>
        <li class="substep">If the issue persists, contact KTWG support for further assistance.</li>
      </ul>
    </section>

    <div class="brand-mark"><span class="square"></span>KTWG</div>
  </main>
</body>
</html>
```